Shopping center investment profile

We need to design a two-page 8.5" x 11" brochure that can be used as a template for profiling our shopping centers and demonstrating our track record to investors.

Our company (QLM Real Estate Investments) owns retail shopping centers in the southwestern United States. Our website is www.qlmvx.example, but we will be redesigning and modernizing the website and logo in the near future, so please do not use the color schemes or framework of the website for the brochure.

Our investors are institutional and high net worth investors who typically have an existing relationship with our company. They are determining whether to invest multi-millions of dollars in a shopping center opportunity, so the brochure needs to be professional, very high quality and provide key information about the specific property.
Updates

Additional guidance on color scheme:

We would like to see a Blue (something like Hex #5A61BC) and Gold (Hex #EDB215) or (Hex #DDA24B) color scheme with some Black accents 

Thank you!

Target Market(s)

Our target audiences are institutional investors, high net-worth individuals, financial firms and medium to large commercial real estate companies.

Industry/Entity Type

Investment

Requirements
Must have
• Clean and modern look with corresponding fonts and colors.
• Incorporates the information found in the attached "Harborline Commons profile" Pages or PDF file.
• Final file design files that can be modified easily
Nice to have
• Two examples of industry brochures are attached. These are examples of the professional quality that we are looking for, not necessarily the design or format.

```html
<!DOCTYPE html>
<html lang="en">
<head>
<meta charset="utf-8">
<title>Harborline Commons – Property Profile</title>
<link href="https://fonts.googleapis.com/css2?family=Cinzel:wght@400;600;700&family=Crimson+Text:wght@400;600;700&family=Arimo:wght@400&display=swap" rel="stylesheet">
<style>
  :root{
    --stage:#000;
    --gold:#e0a24a;
    --gold-light:#e9b868;
    --gold-stripe:#d8963e;
    --blue:#5a61a8;
    --blue-deep:#4a5096;
    --navy-text:#2f3480;
    --paper:#e8e9eb;
    --white:#fff;
  }
  *{margin:0;padding:0;box-sizing:border-box}
  html,body{width:1200px;height:735px;overflow:hidden;background:var(--stage)}
  .canvas{position:relative;width:1200px;height:735px}
  .page{position:absolute;top:63px;width:459px;height:595px;background:var(--paper);overflow:hidden}
  .page--front{left:104px}
  .page--back{left:630px}
  .abs{position:absolute}
  .stripes{background:repeating-linear-gradient(180deg,var(--gold-light) 0 11px,var(--gold-stripe) 11px 22px)}
  .gold-band{background:var(--gold)}
  .heading-caps{font-family:"Cinzel",serif;font-weight:600;letter-spacing:.04em}
  .serif{font-family:"Crimson Text",serif}
  .sans{font-family:"Arimo",Arial,sans-serif}

  /* front */
  .front-top{left:0;top:0;width:459px;height:92px}
  .front-top-stripes{left:0;top:0;width:62px;height:92px}
  .front-column{left:62px;top:0;width:118px;height:307px;background:linear-gradient(180deg,var(--blue) 0%,#6d73b0 65%,#c7c9e0 100%)}
  .profile-label{left:64px;top:3px;font-size:11px;color:var(--navy-text)}
  .front-title{left:64px;top:54px;font-size:30px;letter-spacing:.02em;color:var(--white);white-space:nowrap;font-weight:700}
  .photo{left:134px;top:103px;width:304px;height:202px;background:linear-gradient(180deg,#2e3566 0%,#55557a 45%,#8a6a4a 70%,#3c3a3e 100%);box-shadow:3px 3px 8px rgba(0,0,0,.45)}
  .opportunity{left:0;top:307px;width:180px;height:273px;background:linear-gradient(180deg,var(--blue-deep) 0%,#6b71ae 60%,#a6a9cd 100%);padding:14px 2px 0 9px}
  .opportunity h2{font-size:16px;color:var(--white);text-align:center;font-weight:600;margin-bottom:11px}
  .bullets{list-style:none}
  .bullets li{font-size:8px;line-height:10px;color:var(--white);margin-bottom:9px;padding-left:6px;position:relative}
  .bullets li::before{content:"";position:absolute;left:0;top:3px;width:3px;height:3px;background:var(--white)}
  .facts{left:180px;top:307px;width:259px;height:273px;padding:35px 14px 0 0;text-align:right}
  .facts .row{display:block;height:22px}
  .facts span{display:inline-block;font-size:12px;line-height:16px;font-weight:700;color:var(--navy-text);border-bottom:1px solid var(--navy-text);white-space:nowrap}
  .facts .row:last-child span{border-bottom:none;font-size:11.5px}
  .brand-box{left:278px;top:500px;width:181px;height:80px;background:linear-gradient(180deg,#5b62a8,#7b80b8);padding:24px 0 0 12px;color:var(--white)}
  .brand-name{font-family:"Crimson Text",serif;font-weight:700;font-size:28px;line-height:28px}
  .brand-sub{font-size:12px;margin-top:4px;letter-spacing:.03em}
  .footer-bar{left:0;top:580px;width:459px;height:15px;background:var(--blue);color:var(--white);font-size:10px;font-weight:700;padding:1px 0 0 12px;letter-spacing:.03em}

  /* back */
  .back-top{left:0;top:0;width:459px;height:92px}
  .back-top-stripes{left:345px;top:0;width:114px;height:92px}
  .back-title{left:37px;top:19px;font-size:22px;color:var(--white);font-weight:700;white-space:nowrap}
  .section-title{left:70px;top:72px;font-size:13px;color:var(--navy-text)}
  .challenges{left:69px;top:99px;width:272px}
  .challenges p{font-size:8.4px;line-height:14px;color:var(--navy-text);margin-bottom:8px}
  .challenges p:nth-child(3){margin-top:12px}
  .challenges b{font-weight:700}
  .back-column{left:342px;top:92px;width:117px;height:213px;background:linear-gradient(180deg,#d9dae6 0%,#6c72ad 35%,var(--blue) 100%)}
  .back-edge{left:0;top:212px;width:20px;height:93px;background:linear-gradient(180deg,var(--gold),#f1dab0)}
  .back-edge-blue{left:0;top:305px;width:20px;height:229px;background:linear-gradient(180deg,var(--blue) 0%,#eef0f5 100%)}
  .investment{left:20px;top:305px;width:258px;height:229px;padding:4px 10px 0 0}
  .investment h2{font-size:12.5px;color:var(--navy-text);text-align:right;margin-bottom:10px}
  .invest-row{font-size:12.5px;font-weight:700;color:var(--navy-text);text-align:right;height:22px;white-space:nowrap}
  .invest-row--total{padding-right:44px}
  .structure{display:flex;gap:26px;padding-left:55px;font-weight:700;color:var(--navy-text)}
  .structure .label{font-size:12.5px}
  .structure ul{list-style:none;font-size:7.5px;line-height:11.5px;margin-top:2px}
  .results{left:278px;top:305px;width:181px;height:229px;background:linear-gradient(180deg,var(--blue-deep),#6d73ae);padding:14px 4px 0 10px}
  .results h2{font-size:16px;color:var(--white);text-align:center;font-weight:600;margin-bottom:10px}
  .results .bullets li{font-size:9.2px;line-height:11.5px;margin-bottom:10px}
  .back-footer{left:0;top:534px;width:459px;height:61px;background:linear-gradient(180deg,#5e64a8 0%,var(--blue) 60%,#c99a55 100%);padding:12px 0 0 22px;color:var(--white)}
</style>
</head>
<body>
<main class="canvas">
  <section class="page page--front">
    <div class="abs gold-band front-top"></div>
    <div class="abs stripes front-top-stripes"></div>
    <div class="abs front-column"></div>
    <div class="abs heading-caps profile-label">Property Profile</div>
    <h1 class="abs heading-caps front-title">Harborline Commons</h1>
    <div class="abs photo" role="img" aria-label="Dusk photo of the shopping center storefront with illuminated grocery windows"></div>

    <div class="abs opportunity">
      <h2 class="heading-caps">Opportunity</h2>
      <ul class="bullets sans">
        <li>Bank owned property with attractive purchase price</li>
        <li>Strong relationship with seller's broker and decision makers</li>
        <li>Redevelopment upside with management and leasing</li>
        <li>No major renovations required</li>
        <li>Marlow location has very strong population, education and income demographics</li>
        <li>Adjacent to premier 2,500-residence master planned community of Vista Palms</li>
        <li>Strong employment area with the new Meridian Gateway hospital and the adjacent Lakeside Cancer center</li>
      </ul>
    </div>

    <div class="abs stripes facts serif">
      <div class="row"><span>Shopping Center</span></div>
      <div class="row"><span>79.490 SQ FT</span></div>
      <div class="row"><span>Purchased April 2011</span></div>
      <div class="row"><span>Total Investment $X,XXX,XXX</span></div>
      <div class="row"><span>Purchase Occupancy 8.39%</span></div>
      <div class="row"><span>Current Occupancy 97.29%</span></div>
      <div class="row"><span>Projected 5-year IRR (Unleveraged) XX.XX%</span></div>
    </div>

    <div class="abs brand-box">
      <div class="brand-name">QLM</div>
      <div class="brand-sub heading-caps">Real Estate Investments</div>
    </div>
    <div class="abs footer-bar serif">http://www.qlmvx.example</div>
  </section>

  <section class="page page--back">
    <div class="abs gold-band back-top"></div>
    <div class="abs stripes back-top-stripes"></div>
    <h1 class="abs heading-caps back-title">Harborline Commons</h1>
    <h2 class="abs heading-caps section-title">Challenges and Solutions</h2>
    <div class="abs challenges serif">
      <p><b>Nationwide vacancy rate</b> - QLM did significant due diligence on the property before purchasing the asset, and determined that the location is an A/A-; Tenant improvement and leasing commissions were reserved in order to attract national and regional tenants</p>
      <p><b>Size of Anchor space</b> - QLM determined that a family-friendly entertainment venue would best serve the demographics in the area instead of another grocer; QLM sought out an experienced operator in Lucky Lanes, who has multiple locations in three states</p>
      <p><b>Curb Appeal</b> - With vacancy and a stigma attached to the center, QLM had to change the center's appeal to the community. QLM worked hand in hand with the Town of Marlow and the Vista Palms community association to paint the center, upgrade landscaping and add new and larger monument signs</p>
    </div>
    <div class="abs back-column"></div>
    <div class="abs back-edge"></div>
    <div class="abs back-edge-blue"></div>

    <div class="abs stripes investment serif">
      <h2 class="heading-caps">Investment Information</h2>
      <div class="invest-row">Purchase Price $X,XXX,XXX</div>
      <div class="invest-row">Sponsor Acquisition Fee $XX,XXX</div>
      <div class="invest-row">Painting and Landscape $XXX,XXX</div>
      <div class="invest-row">TI/LC Reserve $X,XXX,XXX</div>
      <div class="invest-row">Operating Expenses $XXX,XXX</div>
      <div class="invest-row invest-row--total">Total Cash Investment</div>
      <div class="invest-row">Investor / Sponsor Split XX% / XX%</div>
      <div class="structure">
        <span class="label">Structure</span>
        <ul>
          <li>• Cash Flow Pari Passu</li>
          <li>• Acquisition Fee</li>
          <li>• Management Fee</li>
        </ul>
      </div>
    </div>

    <div class="abs results">
      <h2 class="heading-caps">Results</h2>
      <ul class="bullets sans">
        <li>Stabilized the shopping center within three years, producing excellent results for investors</li>
        <li>Transformed the center into a vibrant destination that the surrounding community is excited about</li>
        <li>Transitioned legacy tenants to upgrade the business operators</li>
        <li>Reduced the shopping center's operating expenses by replacing vendors and appealing property taxes</li>
      </ul>
    </div>

    <div class="abs back-footer">
      <div class="brand-name">QLM</div>
      <div class="brand-sub heading-caps">Real Estate Investments</div>
    </div>
  </section>
</main>
</body>
</html>
```